Business card design for holistic health care clinic

We need a double-sided business card design for our holistic health care clinic that integrates our logo design and also its color scheme. My business is called Valmira. It is an integrative medicine clinic. You have already done the logo for me. Please ensure an elegant and upscale design that is not cluttered, but still has all the necessary information (please see below for details).

Target Market(s)

Wellness, fitness, rehabilitation for educated, well-traveled open-minded clients who are focused on natural, organic, balanced and preventive healthcare and lifestyle.

Industry/Entity Type

Medical

Contact Information for Business Card

Modern, clean.

Number of Pages Required

1 page

Font styles to use
Serif
Sans Serif

Colors

Designer to choose colors to be used in the design.

Requirements
Must have
• Logo on one side, all other information on the other side.
• Other information should include:
• Tobias Wrenfeld - DOE, CPT, LMT
• 4100 East Marrow Drive
• Austin, TX 78119
• 512 555 0148
• 818 555 0192
• info@ValmiraHealth.example
• t.wrenfeld@ValmiraHealth.example
Nice to have
• Darker background on front - but not totally black - shaded/dark gray.

```html
<!DOCTYPE html>
<html lang="en">
<head>
<meta charset="utf-8">
<title>Valmira – Business Card</title>
<link rel="stylesheet" href="https://fonts.googleapis.com/css2?family=PT+Sans:wght@400;700&display=swap">
<style>
  :root {
    --stage: #000000;
    --card: #2f3033;
    --accent: #1b93d6;
    --text: #f1f1f1;
    --rule: #45474b;
  }
  * { margin: 0; padding: 0; box-sizing: border-box; }
  html, body { width: 1200px; height: 900px; overflow: hidden; }
  body {
    position: relative;
    background: var(--stage);
    font-family: "PT Sans", Arial, sans-serif;
  }
  .card {
    position: absolute;
    top: 271px;
    width: 457px;
    height: 281px;
    border-radius: 14px;
    background: var(--card);
  }
  .card--back { left: 137px; }
  .card--front { left: 626px; }

  .brand-mark {
    position: absolute;
    left: 20px;
    top: 122px;
    width: 170px;
    display: flex;
    align-items: center;
    justify-content: center;
    gap: 8px;
    color: var(--accent);
    font-weight: 700;
    font-size: 28px;
  }
  .brand-mark__dot {
    width: 16px; height: 16px;
    border-radius: 50%;
    background: var(--accent);
  }

  .divider {
    position: absolute;
    left: 200px;
    top: 81px;
    width: 1px;
    height: 148px;
    background: var(--rule);
  }

  .holder {
    position: absolute;
    left: 219px;
    top: 56px;
    color: var(--accent);
    font-weight: 700;
    font-size: 16px;
    white-space: nowrap;
  }
  .holder__credentials { font-size: 12px; }

  .address {
    position: absolute;
    left: 216px;
    top: 95px;
    color: var(--text);
    font-size: 12.5px;
    line-height: 19px;
    font-style: normal;
  }

  .contacts {
    position: absolute;
    left: 216px;
    top: 148px;
    list-style: none;
    color: var(--text);
    font-size: 12px;
    line-height: 19px;
    white-space: nowrap;
  }
  .contacts li { display: flex; align-items: center; gap: 7px; }
  .contacts svg { width: 10px; height: 10px; fill: var(--accent); flex: none; }

  .front-logo {
    position: absolute;
    left: 0; right: 0;
    top: 112px;
    text-align: center;
    color: var(--accent);
    font-weight: 700;
    font-size: 50px;
    line-height: 50px;
    letter-spacing: 1px;
  }
  .front-tagline {
    position: absolute;
    left: 0; right: 0;
    top: 169px;
    text-align: center;
    color: var(--accent);
    font-weight: 700;
    font-size: 15px;
  }
</style>
</head>
<body>

<section class="card card--back" aria-label="Business card, contact side">
  <div class="brand-mark"><span class="brand-mark__dot"></span>Valmira</div>
  <div class="divider"></div>

  <h1 class="holder">Tobias Wrenfeld <span class="holder__credentials">- DOE, CPT, LMT</span></h1>

  <address class="address">
    4100 East Marrow Drive<br>
    Austin, TX 78119
  </address>

  <ul class="contacts">
    <li>
      <svg viewBox="0 0 10 10" aria-hidden="true"><path d="M2 0.5 L3.6 2.6 L2.8 3.6 Q4 6 6.4 7.2 L7.4 6.4 L9.5 8 L8.4 9.5 Q4.5 9.3 0.5 1.6 Z"/></svg>
      512 555 0148
    </li>
    <li>
      <svg viewBox="0 0 10 10" aria-hidden="true"><path d="M2.5 0 H7.5 V10 H2.5 Z M3.4 1.2 V8 H6.6 V1.2 Z"/></svg>
      818 555 0192
    </li>
    <li>
      <svg viewBox="0 0 10 10" aria-hidden="true"><path d="M0.5 2 H9.5 V8.5 H0.5 Z" /><path d="M0.5 2 L5 5.5 L9.5 2" fill="none" stroke="#2f3033" stroke-width="0.9"/></svg>
      info@ValmiraHealth.example
    </li>
    <li>
      <svg viewBox="0 0 10 10" aria-hidden="true"><circle cx="5" cy="5" r="4.6"/><path d="M3 2.5 Q4.5 3.5 3.5 5 Q5 6 5.5 8 M6.5 1.5 Q6 3 7.8 4" fill="none" stroke="#2f3033" stroke-width="0.8"/></svg>
      t.wrenfeld@ValmiraHealth.example
    </li>
  </ul>
</section>

<section class="card card--front" aria-label="Business card, logo side">
  <div class="front-logo">Valmira</div>
  <p class="front-tagline">Integrative Holistic Medicine</p>
</section>

</body>
</html>
```